KRT Project Signage

Need a sign to be displayed in the front of properties currently under Construction or Renovation to advertise our company information. Need it to be Professional and Contemporary. We are a Design/Build Construction Company. Information should include Company Name, email, website, phone number. Attached: Logo and company brochure, also included and inspiration images

```html
<!DOCTYPE html>
<html lang="en">
<head>
<meta charset="utf-8">
<title>KRT Project Signage</title>
<link rel="stylesheet" href="https://fonts.googleapis.com/css2?family=Bebas+Neue&family=Poppins:wght@600;700;800&display=swap">
<style>
  :root {
    --sign-yellow: #f2ec48;
    --sign-black: #000000;
    --sign-white: #ffffff;
    --divider-olive: #8a8420;
    --backdrop: #a5a5a5;
  }
  html, body {
    margin: 0;
    padding: 0;
    width: 1200px;
    height: 3200px;
    overflow: hidden;
    background: var(--backdrop);
  }
  .sign {
    position: absolute;
    left: 90px;
    top: 835px;
    width: 1020px;
    height: 1530px;
    background: var(--sign-black);
    overflow: hidden;
    font-family: "Poppins", Arial, sans-serif;
  }
  .sign-shapes {
    position: absolute;
    inset: 0;
    width: 1020px;
    height: 1530px;
  }
  .owner-name {
    position: absolute;
    top: 58px;
    left: 0;
    width: 100%;
    margin: 0;
    text-align: center;
    font-family: "Bebas Neue", Impact, sans-serif;
    font-weight: 400;
    font-size: 172px;
    line-height: 1;
    color: var(--sign-black);
  }
  .owner-role {
    position: absolute;
    top: 216px;
    left: 0;
    width: 100%;
    margin: 0;
    text-align: center;
    font-weight: 700;
    font-size: 44px;
    line-height: 1;
    letter-spacing: 0.2em;
    color: var(--sign-black);
  }
  .contact-row {
    position: absolute;
    left: 137px;
    display: flex;
    align-items: center;
    color: var(--sign-white);
    font-weight: 600;
  }
  .contact-row .icon {
    flex: none;
    width: 48px;
    margin-right: 23px;
  }
  .contact-email { top: 505px; font-size: 50px; line-height: 1.3; }
  .contact-address { top: 660px; font-size: 45px; line-height: 1.4; align-items: flex-start; }
  .contact-address .icon { margin-top: 12px; }
  .divider {
    position: absolute;
    left: 118px;
    width: 787px;
    height: 2px;
    background: var(--divider-olive);
  }
  .divider-first { top: 622px; }
  .divider-second { top: 844px; }
  .mobile-line {
    position: absolute;
    top: 880px;
    left: 129px;
    display: flex;
    align-items: center;
    color: var(--sign-white);
    font-weight: 700;
    font-size: 118px;
    line-height: 1;
  }
  .mobile-line .phone-badge {
    width: 86px;
    height: 86px;
    margin-right: 20px;
  }
  .office-pill {
    position: absolute;
    top: 1024px;
    left: 102px;
    width: 817px;
    height: 106px;
    border-radius: 53px;
    background: var(--sign-yellow);
    display: flex;
    align-items: center;
    overflow: hidden;
    box-sizing: border-box;
    border: 5px solid var(--sign-yellow);
  }
  .office-label {
    height: 100%;
    width: 274px;
    background: var(--sign-white);
    border-radius: 48px 0 0 48px;
    display: flex;
    align-items: center;
    justify-content: center;
    font-weight: 800;
    font-size: 60px;
    color: var(--sign-black);
  }
  .office-number {
    display: flex;
    align-items: center;
    margin-left: 32px;
    font-weight: 700;
    font-size: 64px;
    color: var(--sign-black);
  }
  .office-number .phone-badge {
    width: 62px;
    height: 62px;
    margin-right: 16px;
  }
  .company-name {
    position: absolute;
    top: 1276px;
    left: 0;
    width: 100%;
    margin: 0;
    text-align: center;
    font-weight: 600;
    font-size: 60px;
    line-height: 1.2;
    letter-spacing: 0.04em;
    color: var(--sign-black);
  }
</style>
</head>
<body>
  <main class="sign">
    <svg class="sign-shapes" viewBox="0 0 1020 1530" aria-hidden="true">
      <path d="M0 228 Q510 534 1020 228 V248 Q510 588 0 248 Z" fill="var(--sign-white)"/>
      <rect x="475" y="360" width="71" height="80" fill="var(--sign-black)"/>
      <path d="M0 0 H1020 V202 Q510 514 0 202 Z" fill="var(--sign-yellow)"/>
      <path d="M0 1191 Q510 1050 1020 1191 V1530 H0 Z" fill="var(--sign-yellow)"/>
      <path d="M0 1233 Q510 1048 1020 1233 V1530 H0 Z" fill="var(--sign-white)"/>
    </svg>

    <h1 class="owner-name">MARLOW REYES</h1>
    <p class="owner-role">DESIGN AND BUILDER</p>

    <div class="contact-row contact-email">
      <svg class="icon" viewBox="0 0 48 34" aria-hidden="true">
        <rect x="2" y="2" width="44" height="30" fill="none" stroke="var(--sign-yellow)" stroke-width="4"/>
        <path d="M2 2 L24 20 L46 2 M2 32 L18 16 M46 32 L30 16" fill="none" stroke="var(--sign-yellow)" stroke-width="4"/>
      </svg>
      <span>dana@krtconstruction.com</span>
    </div>

    <div class="divider divider-first"></div>

    <div class="contact-row contact-address">
      <svg class="icon" viewBox="0 0 48 56" aria-hidden="true">
        <path d="M24 4 C14 4 8 11 8 19 C8 30 24 44 24 44 C24 44 40 30 40 19 C40 11 34 4 24 4 Z" fill="none" stroke="var(--sign-yellow)" stroke-width="5"/>
        <circle cx="24" cy="19" r="6" fill="var(--sign-yellow)"/>
        <path d="M6 50 Q24 56 42 50" fill="none" stroke="var(--sign-yellow)" stroke-width="4"/>
      </svg>
      <span>4150 Harbor View Rd., Ste. 310<br>Coral Bay, FL 33990</span>
    </div>

    <div class="divider divider-second"></div>

    <div class="mobile-line">
      <svg class="phone-badge" viewBox="0 0 24 24" aria-hidden="true">
        <circle cx="12" cy="12" r="12" fill="var(--sign-yellow)"/>
        <path transform="translate(3.6 3.6) scale(0.7)" d="M6.6 10.8c1.4 2.8 3.8 5.1 6.6 6.6l2.2-2.2c.3-.3.7-.4 1-.2 1.1.4 2.3.6 3.6.6.6 0 1 .4 1 1V20c0 .6-.4 1-1 1C10.6 21 3 13.4 3 4c0-.6.4-1 1-1h3.5c.6 0 1 .4 1 1 0 1.3.2 2.5.6 3.6.1.3 0 .7-.2 1z" fill="var(--sign-black)"/>
      </svg>
      <span>555.014.2287</span>
    </div>

    <div class="office-pill">
      <div class="office-label">OFFICE</div>
      <div class="office-number">
        <svg class="phone-badge" viewBox="0 0 24 24" aria-hidden="true">
          <circle cx="12" cy="12" r="12" fill="var(--sign-black)"/>
          <path transform="translate(3.6 3.6) scale(0.7)" d="M6.6 10.8c1.4 2.8 3.8 5.1 6.6 6.6l2.2-2.2c.3-.3.7-.4 1-.2 1.1.4 2.3.6 3.6.6.6 0 1 .4 1 1V20c0 .6-.4 1-1 1C10.6 21 3 13.4 3 4c0-.6.4-1 1-1h3.5c.6 0 1 .4 1 1 0 1.3.2 2.5.6 3.6.1.3 0 .7-.2 1z" fill="var(--sign-yellow)"/>
        </svg>
        <span>555.019.6630</span>
      </div>
    </div>

    <p class="company-name">KRT CONSTRUCTION</p>
  </main>
</body>
</html>
```